New Business Card Design Project

I need a design for business cards, i am an electrical business called "Corvane Electrical and Communications" i need the cards to be double sided with the company logo on the back (attached) the front needs to say my company name, web site, email address, telephone number, and ABN number and electrical license number. I am open to different arrangements of the information but would like the background to be incorporating something electrical or something that looks smart. open to all additional ideas also.

The company colours are orange and grey see logo attached.

Business Name: Corvane Electrical and Communications
Website: corvaneelectricalandcomms.example.com.au
Email: brent@corvaneelectricalandcomms.example.com.au
Telephone(mobile): 0481209736
ABN: 71208349162
Lic No: 418273D

Target Market(s)

Business entities, Project Managers, Accounts, Clients

Industry/Entity Type

Electrician

Contact Information for Business Card

I need a design for business cards, i am an electrical business called "Corvane Electrical and Communications" i need the cards to be double sided with the company logo on the back (attached) the front needs to say my company name

Font styles to use
Serif
Sans Serif

Colors
f37122
5c5c5c

Requirements
Must have
• Must have the Logo on the back open to different ways of it being on the back but had in mind to keep it central but again open to other options
Nice to have
• A real modern cool background that is eye catching yet contemporary
Should not have
• No backgrounds of a light bulb or plug or anything like that

```html
<!DOCTYPE html>
<html lang="en">
<head>
<meta charset="utf-8">
<title>Corvane Electrical and Communications – Business Card</title>
<link rel="stylesheet" href="https://fonts.googleapis.com/css2?family=Quicksand:wght@400;500;600&display=swap">
<style>
  :root {
    --page: #e7e5e1;
    --card-grey: #5b5c5e;
    --card-white: #f7f7f6;
    --accent: #e9b31c;
    --text-grey: #5c5c5c;
    --text-dark: #4a4a4c;
  }
  * { margin: 0; padding: 0; box-sizing: border-box; }
  html, body {
    width: 1200px; height: 780px; overflow: hidden;
    background: var(--page);
    font-family: "Quicksand", sans-serif;
  }
  .sheet {
    position: relative; width: 1200px; height: 780px;
    display: flex; flex-direction: column; align-items: center; justify-content: center;
    gap: 40px;
  }
  .card {
    position: relative; width: 600px; height: 340px;
    border-radius: 18px; overflow: hidden;
    box-shadow: 0 6px 18px rgba(0,0,0,0.18);
  }
  .card-bg { position: absolute; inset: 0; width: 100%; height: 100%; }
  .card-content { position: absolute; inset: 0; }

  /* Front */
  .front .card-content {
    display: flex; flex-direction: column; justify-content: center;
    padding-left: 92px; padding-right: 60px;
  }
  .person-name { font-size: 27px; font-weight: 500; color: var(--text-grey); line-height: 1.1; }
  .person-role { font-size: 17px; font-weight: 500; color: var(--accent); margin-bottom: 22px; }
  .contact-line { font-size: 15px; font-weight: 500; color: var(--text-grey); line-height: 1.55; white-space: nowrap; }
  .contact-line .label { color: var(--accent); font-weight: 600; }
  .contact-line .divider { color: var(--text-grey); margin: 0 6px; }
  .website { font-size: 15px; font-weight: 500; color: var(--accent); margin-top: 20px; white-space: nowrap; }

  /* Back */
  .back .card-content {
    display: flex; flex-direction: column; align-items: center; justify-content: center;
    padding: 0 70px;
  }
  .brand {
    display: flex; align-items: center; gap: 18px;
  }
  .brand-mark { width: 24px; height: 24px; border-radius: 50%; background: var(--accent); flex: none; }
  .brand-name {
    font-size: 32px; font-weight: 500; color: var(--text-grey); line-height: 1.2;
    text-align: left;
  }
  .brand-web {
    display: flex; align-items: center; gap: 14px; margin-top: 26px;
    font-size: 15px; font-weight: 500; color: var(--text-dark); white-space: nowrap;
  }
  .brand-web .rule { width: 44px; height: 2px; background: var(--accent); }
</style>
</head>
<body>
<main class="sheet">

  <section class="card front" aria-label="Business card front">
    <svg class="card-bg" viewBox="0 0 600 340" preserveAspectRatio="none" aria-hidden="true">
      <rect width="600" height="340" fill="var(--card-grey)"/>
      <path d="M0 62 Q300 -28 600 62 L600 278 Q300 368 0 278 Z" fill="var(--card-white)"/>
      <path d="M0 62 Q300 -28 600 62" fill="none" stroke="var(--accent)" stroke-width="3"/>
      <path d="M0 278 Q300 368 600 278" fill="none" stroke="var(--accent)" stroke-width="3"/>
    </svg>
    <div class="card-content">
      <p class="person-name">Employee Name</p>
      <p class="person-role">Principal</p>
      <p class="contact-line"><span class="label">P:</span> 0481209736</p>
      <p class="contact-line"><span class="label">E:</span> brent@corvaneelectricalandcomms.example.com.au</p>
      <p class="contact-line"><span class="label">ABN:</span> 71208349162<span class="divider">|</span><span class="label">Lic No:</span> 418273D</p>
      <p class="website">corvaneelectricalandcomms.example.com.au</p>
    </div>
  </section>

  <section class="card back" aria-label="Business card back">
    <svg class="card-bg" viewBox="0 0 600 340" preserveAspectRatio="none" aria-hidden="true">
      <rect width="600" height="340" fill="var(--card-grey)"/>
      <path d="M0 62 Q300 -28 600 62 L600 278 Q300 368 0 278 Z" fill="var(--card-white)"/>
      <path d="M0 62 Q300 -28 600 62" fill="none" stroke="var(--accent)" stroke-width="3"/>
      <path d="M0 278 Q300 368 600 278" fill="none" stroke="var(--accent)" stroke-width="3"/>
    </svg>
    <div class="card-content">
      <div class="brand">
        <span class="brand-mark"></span>
        <p class="brand-name">Corvane Electrical<br>and Communications</p>
      </div>
      <p class="brand-web"><span class="rule"></span>corvaneelectricalandcomms.example.com.au<span class="rule"></span></p>
    </div>
  </section>

</main>
</body>
</html>
```